Fine Art business needs new website

We need a simple website with a home page, about us page, New sculptures, Sold sculptures, and a contact us page.Our sculptures are very high end one of a kind pieces. As such we need the site to be VERY elegant and professional. Lastly, because I'll be updating pictures on the website on a monthly basis it needs to be user friendly to update (Wordpress is preferred). The only branding we have so far for the business is a business card.
Updates
I wasn't completely ready when this project launched, also I am on the road right now and haven't been able to be as responsive to all you designers as I would like. I will work on giving feedback to all the top designs we've received so far. Thank you all so much for your participation and hardwork.
Target Market(s)
High end customers (affluent), art collectors, interior decorators/designers
Industry/Entity Type
Art Gallery
Coding
Coded - Design and coding required
Number of Pages Required
5+ page
Requirements
Must have
- Easily editable picture gallery for myself so that I can add new pieces(pictures of the pieces), remove sold pieces, etc. I would like the website to be built in wordpress so I can update it. I currently use mangewordpress through Netmarro for my other business website and would like to do the same for this one.
- Pages:
- -Intro page with featured pieces
- -Current pieces gallery (for sale) mainly a picture gallery
- -Sculptures archive (sold pieces) another picture gallery
- -About us: Pull-down of -about the artist (attached content)
- -Artistic Process (attached content)
- -Show Schedule:
- -one page dedicated to "friends of TMV" (basically a link page)
- TO BE CLEAR "www.pineroverslane.com" IS A TOTALLY DIFFERENT SITE AND I'M NOT TRYING TO COMBINE THE TWO OR JOIN THEM INTO ONE. This page needs be more elegant and seperate from The Pine Rovers site.
- UPDATE: I'd like a link to the TMV Facebook page: https://www.faceplume-social.com/mirelcraftworks/
Nice to have
- I would like the pictures on the gallery pages able to have text connected with them (Materials, price)
- I would like the site style and fonts to be similar to our business cards we've already had designed (picture attached).
Should not have
- Too much flash or other things that will make the site slow to load.

```html
<!DOCTYPE html>
<html lang="en">
<head>
<meta charset="utf-8">
<title>Tallis Marble Vault</title>
<link rel="stylesheet" href="https://fonts.googleapis.com/css2?family=Cormorant+Garamond:wght@500&family=Montserrat:wght@400;500;700;800&display=swap">
<style>
  :root {
    --paper: #ffffff;
    --ink: #262626;
    --ink-soft: #3a3a3a;
    --frame: #1b1b1b;
    --tag: #e8e8e8;
    --rule: #888888;
    --rule-light: #e2e2e2;
    --amethyst: #6a4bb5;
    --amethyst-deep: #3c2a78;
    --jade: #7fb39a;
    --jade-deep: #3f6f58;
    --geode: #7f93d0;
    --geode-deep: #4a4f7e;
    --malachite: #2f9a62;
    --malachite-deep: #155638;
  }
  * { margin: 0; padding: 0; box-sizing: border-box; }
  html, body { width: 1200px; height: 1200px; overflow: hidden; background: var(--paper); }
  body { position: relative; font-family: "Montserrat", sans-serif; color: var(--ink); }

  .brand {
    position: absolute; left: 56px; top: 34px;
    font-family: "Cormorant Garamond", serif; font-weight: 500;
    font-size: 21px; letter-spacing: 0.09em; color: var(--ink);
  }
  .main-nav { position: absolute; top: 43px; left: 0; width: 1200px; }
  .main-nav a {
    position: absolute; font-size: 9.5px; font-weight: 500;
    letter-spacing: 0.14em; color: var(--ink); text-decoration: none; white-space: nowrap;
  }
  .nav-tools { position: absolute; top: 44px; left: 1146px; display: flex; gap: 6px; align-items: center; }
  .nav-tools span { width: 1px; height: 8px; background: var(--rule-light); }

  .hero-copy { position: absolute; left: 56px; top: 206px; }
  .hero-kicker { font-size: 14px; font-weight: 400; color: var(--ink); }
  .hero-title {
    margin-top: 10px; font-size: 31px; font-weight: 800;
    letter-spacing: 0.29em; color: var(--ink);
  }
  .slide-dots { position: absolute; left: 58px; top: 331px; display: flex; gap: 3px; }
  .slide-dots i { display: block; width: 30px; height: 2px; background: var(--rule); }
  .slide-dots i:first-child { background: var(--rule-light); }

  .hero-image {
    position: absolute; left: 421px; top: 85px; width: 779px; height: 372px;
    background: radial-gradient(ellipse 17% 50% at 64% 46%, var(--amethyst) 0%, var(--amethyst-deep) 55%, #2a2340 80%, var(--frame) 100%);
  }

  .section-title {
    position: absolute; top: 522px; left: 0; width: 1225px; text-align: center;
    font-size: 37px; font-weight: 700; letter-spacing: 0.31em; color: var(--ink);
  }
  .section-sub { position: absolute; top: 586px; left: 641px; display: flex; align-items: center; }
  .section-sub .line { width: 89px; height: 1px; background: var(--ink); margin-right: 8px; }
  .section-sub .tag {
    width: 352px; height: 19px; background: var(--tag);
    font-size: 13px; color: var(--ink-soft); padding-left: 7px; line-height: 20px;
  }

  .piece { position: absolute; background: var(--frame); }
  .piece-jade { left: 106px; top: 731px; width: 480px; height: 223px;
    background: linear-gradient(90deg, var(--frame) 40%, var(--jade-deep) 44%, var(--jade) 48%, #c9dccf 52%, var(--jade-deep) 56.5%, var(--frame) 59%); }
  .piece-geode { left: 106px; top: 982px; width: 480px; height: 240px;
    background: radial-gradient(ellipse 23% 75% at 49% 70%, var(--geode) 0%, var(--geode-deep) 60%, #2c2d40 82%, var(--frame) 100%); }
  .piece-malachite { left: 611px; top: 730px; width: 480px; height: 490px;
    background: radial-gradient(ellipse 27% 58% at 50% 50%, var(--malachite) 0%, var(--malachite-deep) 60%, #17301f 82%, var(--frame) 100%); }
</style>
</head>
<body>
  <header>
    <div class="brand">TALLIS MARBLE VAULT</div>
    <nav class="main-nav">
      <a href="#" style="left:420px">HOME</a>
      <a href="#" style="left:517px">NEW SCULPTURES</a>
      <a href="#" style="left:678px">SOLD SCULPTURES</a>
      <a href="#" style="left:843px">ABOUT</a>
      <a href="#" style="left:944px">THE PINE ROVERS</a>
    </nav>
    <div class="nav-tools">
      <svg width="9" height="8" viewBox="0 0 9 8" aria-label="Cart"><path d="M0 1h2l1 4h5l1-3H2.5" fill="none" stroke="#262626" stroke-width="0.9"/><circle cx="3.5" cy="7" r="0.7" fill="#262626"/><circle cx="7" cy="7" r="0.7" fill="#262626"/></svg>
      <span></span>
      <svg width="7" height="7" viewBox="0 0 7 7" aria-label="Search"><circle cx="3" cy="3" r="2" fill="none" stroke="#262626" stroke-width="1"/><path d="M4.5 4.5L6.5 6.5" stroke="#262626" stroke-width="1"/></svg>
    </div>
  </header>

  <section class="hero">
    <div class="hero-copy">
      <p class="hero-kicker">Designed to perfection</p>
      <h1 class="hero-title">EXQUISITE</h1>
    </div>
    <div class="slide-dots"><i></i><i></i><i></i></div>
    <div class="hero-image" role="img" aria-label="Amethyst crystal sculpture on a round stone and wood pedestal against a dark backdrop"></div>
  </section>

  <section class="gallery">
    <h2 class="section-title">NEW SCULPTURES</h2>
    <div class="section-sub"><span class="line"></span><span class="tag">CURRENT PIECES GALLERY</span></div>
    <div class="piece piece-jade" role="img" aria-label="Tall polished green jade column sculpture with pale veining"></div>
    <div class="piece piece-geode" role="img" aria-label="Blue and violet geode sculpture with crystal cavities"></div>
    <div class="piece piece-malachite" role="img" aria-label="Polished banded malachite freeform sculpture"></div>
  </section>
</body>
</html>
```